Sunset Harbor Living Web Page

We need a web page design that has two intro pages - first being a 'home page', then a link to the second page that has the 'content tabs' and a 'call to action' (see below).

The business helps people that wish to retire to S.E.Asia (Thailand, Malaysia, Indonesia,The Philippines etc) - to enjoy the lifestyle and the remaining years of their lives. What attracts S.E.Asia to many people is the lower cost, the atmoshpere and beauty of the tropics and the vibrancy of the various countries.

People that are wishing to make the most of their retirement and are adventurous at a great bargain compared to the cost of their own countries will be interested.

We help them achieve this - visa, financials (tax, gov't payments etc), introduce them to the right people for property, clubs, retirement facilities, insurance and so forth.

Therefore we are providing an extremely wide ranging service and this site will provide broad but general information only - with a call to action to come and see us for more specific information and how we can help them specifically.

This site will be predominantly for travel and lifestyle, it will be linked with another financial services (financial planning) site later down the track.

The colour scheme is dark green and blue - as per the attached logo design. Photos and background just think lifestyle and S.E.Asia - beaches/mountains/water/recreational activities for retirees.

Target market is mostly those coming up to retirement to those that are already retired. But we also expect to have some interest with younger people that would like to find out more and plan for the future. So a broad age group but I would say mostly 40-70 yrs old.

On the first (Home) page we would like our company name 'Sunset Harbor Living', our logo (which will be on all pages) and a statement such as: “Imagine a retirement where your dreams are brought to life, and you have never felt more alive. Let us show you how”. Then a link to the second page.

We would like an uncluttered site. On the second (contents) page the tabs would be:

- Visa
- Property
- Financials
- Travel
- Insurance & Healthcare
- Medical Tourism
- Cost of living
- Weekly Blogs and articles
- Sunset Harbor Living story

We would also like a call to action on the second page - asking them to leave their contact details if they wish to learn more or sign up to our weekly newsletter/blog.

We are open to suggestions and your imaginations.

Thank you
Malcolm

Font styles to use
Serif
Script

Colors
0255a3
3377b5
00a990
9bcb3c
abd036
33b8a4
85abd2
cadf82
86cfc6

Requirements
Must have
• I have been asked by the web designer to receive a 'Web Font' so that we can 'get off of Zentrofy'. Hope that makes sense.

```html
<!DOCTYPE html>
<html lang="en">
<head>
<meta charset="utf-8">
<title>Sunset Harbor Living</title>
<link href="https://fonts.googleapis.com/css2?family=Raleway:wght@400;500;600;700;800&family=Open+Sans:wght@400;600&display=swap" rel="stylesheet">
<style>
:root{
  --blue:#3377b5;
  --blue-dark:#0255a3;
  --blue-band-top:#5d90c8;
  --blue-band-bottom:#2b5f9e;
  --green:#9bcb3c;
  --green-btn:#7fae3a;
  --ink:#2b2b2b;
  --muted:#777;
  --footer:#262626;
  --white:#fff;
}
*{margin:0;padding:0;box-sizing:border-box}
html,body{width:1200px;height:2359px;overflow:hidden;background:var(--white)}
body{position:relative;font-family:"Open Sans",Arial,sans-serif;color:var(--ink)}
.abs{position:absolute}
.heading{font-family:"Raleway",Arial,sans-serif}

/* header */
.site-header{top:0;left:0;width:1200px;height:157px;background:var(--white)}
.brand{left:98px;top:52px;display:flex;align-items:center;gap:12px}
.brand-dot{width:44px;height:44px;border-radius:50%;background:var(--green)}
.brand-name{font-family:"Raleway",sans-serif;font-weight:700;font-size:23px;color:var(--blue-dark)}
.contact{display:flex;align-items:center;gap:14px;font-family:"Raleway",sans-serif}
.contact-label{font-size:12px;color:#444}
.contact-value{font-size:15px;color:var(--blue);margin-top:3px}
.contact-value.small{font-size:12px;color:#444}
.search{left:1053px;top:53px;width:48px;height:48px;border-radius:50%;background:#ececec;display:flex;align-items:center;justify-content:center}

/* nav */
.main-nav{top:157px;left:0;width:1200px;height:52px;background:var(--blue);border-bottom:3px solid var(--green)}
.main-nav ul{list-style:none;display:flex;gap:14px;padding-left:98px;height:100%;align-items:center}
.main-nav li{font-family:"Raleway",sans-serif;font-weight:600;font-size:10px;color:var(--white);text-transform:uppercase;position:relative;white-space:nowrap}
.main-nav li.active{color:var(--green)}
.main-nav li.active::after{content:"";position:absolute;left:50%;bottom:-20px;margin-left:-5px;border:5px solid transparent;border-bottom-color:var(--green)}

/* hero */
.hero{top:209px;left:0;width:1200px;height:600px;background:linear-gradient(100deg,#3a3530 0%,#5d5650 45%,#8a8178 70%,#4f4943 100%)}
.hero-title{left:98px;top:345px;font-weight:800;font-size:41px;color:var(--white);letter-spacing:.5px}
.hero-sub{left:98px;top:402px;font-weight:700;font-size:16px;color:var(--white);line-height:35px;text-transform:uppercase}
.hero-sub em{font-style:normal;color:var(--green)}
.hero-accent{left:98px;top:500px;width:340px;height:70px;border-radius:6px;background:var(--green)}
.hero-arrow{top:450px;width:20px;height:56px}
.hero-wave{top:700px;left:0;width:1200px;height:230px}

/* welcome */
.section-title{width:1200px;left:0;text-align:center;font-family:"Raleway",sans-serif;font-weight:700;font-size:24px;color:var(--ink)}
.title-accent{width:96px;height:16px;left:552px;border-radius:3px;background:var(--blue)}
.title-accent.light{background:var(--white)}
.welcome-text{left:138px;top:894px;width:924px;text-align:center;font-size:12.3px;line-height:25px;color:var(--muted)}
.feature{display:flex;gap:20px;top:998px;width:340px}
.feature-icon{width:66px;height:66px;border-radius:50%;border:2px solid var(--green);flex:none;display:flex;align-items:center;justify-content:center}
.feature h3{font-family:"Raleway",sans-serif;font-weight:600;font-size:13.5px;color:#333;margin:12px 0 6px}
.feature p{font-size:11px;line-height:19px;color:var(--muted)}

/* destinations */
.destinations{top:1121px;left:0;width:1200px;height:534px;background:linear-gradient(var(--blue-band-top),var(--blue-band-bottom))}
.destinations .section-title{color:var(--white)}
.card{top:1285px;width:231px;height:311px;background:var(--white);text-align:center}
.card-photo{margin:8px;height:157px}
.card h3{font-family:"Raleway",sans-serif;font-weight:600;font-size:14px;margin-top:18px;color:#222}
.card p{font-size:11px;line-height:20px;color:var(--muted);margin-top:6px}
.btn-more{display:inline-block;margin-top:14px;width:130px;height:36px;line-height:36px;background:linear-gradient(#8fbf45,var(--green-btn));color:var(--white);font-size:12px;border:1px solid #6d9a2f}

/* blog */
.post{top:1812px;display:flex;gap:20px;width:510px}
.post-photo{width:189px;height:141px;border:5px solid #f3f3f3;flex:none}
.post h4{font-family:"Raleway",sans-serif;font-weight:700;font-size:12px;color:#222;margin-top:6px;white-space:nowrap}
.post-date{font-size:10.5px;color:var(--green);margin-top:8px;text-transform:uppercase}
.post-text{font-size:11px;line-height:21px;color:var(--muted);margin-top:8px}
.post-meta{display:flex;align-items:center;gap:16px;margin-top:12px;font-size:11px;color:var(--muted)}
.stars{color:#f3b51d;letter-spacing:1px;font-size:12px}

/* newsletter */
.newsletter-band{top:1935px;left:0;width:1200px;height:280px}
.news-label{left:171px;top:2106px;font-family:"Raleway",sans-serif;color:var(--white)}
.news-label span{display:block;font-size:17px;font-weight:500}
.news-label strong{display:block;font-size:23px;font-weight:700;margin-top:2px}
.field{top:2114px;width:296px;height:39px;background:var(--white);font-size:11px;color:#666;padding-left:24px;line-height:39px;text-transform:uppercase}
.btn-signup{left:975px;top:2114px;width:126px;height:39px;background:var(--blue);color:var(--white);font-family:"Raleway",sans-serif;font-weight:700;font-size:13px;text-align:center;line-height:39px}

/* footer */
.site-footer{top:2210px;left:0;width:1200px;height:149px;background:var(--footer);text-align:center;color:#cfcfcf;font-family:"Raleway",sans-serif}
.socials{display:flex;justify-content:center;gap:6px;margin-top:19px}
.socials span{width:31px;height:31px;border-radius:50%;border:1.5px solid #777}
.footer-links{font-size:9.5px;text-transform:uppercase;line-height:22px;margin-top:12px;font-weight:500}
.copyright{font-size:9.5px;margin-top:6px;text-transform:uppercase}
</style>
</head>
<body>

<header class="site-header abs">
  <div class="brand abs"><span class="brand-dot"></span><span class="brand-name">Sunset Harbor Living</span></div>
  <div class="contact abs" style="left:650px;top:58px">
    <svg width="22" height="34" viewBox="0 0 22 34"><rect x="2" y="1" width="18" height="32" rx="3" fill="none" stroke="#3377b5" stroke-width="3"/><rect x="5" y="6" width="12" height="19" fill="#3377b5"/><circle cx="11" cy="29" r="1.6" fill="#3377b5"/></svg>
    <div><div class="contact-label">Phone:</div><div class="contact-value">(+100) 555-0142</div></div>
  </div>
  <div class="contact abs" style="left:834px;top:58px">
    <svg width="26" height="34" viewBox="0 0 26 34"><path d="M13 1C6 1 1 6 1 13c0 9 12 20 12 20s12-11 12-20C25 6 20 1 13 1z" fill="#3377b5"/><circle cx="13" cy="13" r="4.5" fill="#fff"/></svg>
    <div><div class="contact-label">Location:</div><div class="contact-value small">45 Palm Harbor Road</div></div>
  </div>
  <div class="search abs"><svg width="12" height="12" viewBox="0 0 12 12"><circle cx="5" cy="5" r="3.5" fill="none" stroke="#9bcb3c" stroke-width="1.8"/><path d="M7.6 7.6L11 11" stroke="#9bcb3c" stroke-width="1.8"/></svg></div>
</header>

<nav class="main-nav abs">
  <ul>
    <li class="active">Home</li><li>Visa Property</li><li>Financials</li><li>Travel</li><li>Insurance &amp; Healthcare</li><li>Medical Tourism</li><li>Cost of Living</li><li>Weekly Blogs and Articles</li><li>Sunset Harbor Living Story</li><li>Contact Us</li>
  </ul>
</nav>

<section class="hero abs" role="img" aria-label="Photo of a smiling retired couple looking at a map in an old city"></section>
<h1 class="hero-title heading abs">IMAGINE A RETIREMENT</h1>
<p class="hero-sub heading abs">Where <em>your dreams are brought</em> to life and<br>you have never felt more alive. Let us show you how</p>
<div class="hero-accent abs" role="img" aria-label="Green painted brush ornament"></div>
<svg class="hero-arrow abs" style="left:56px" viewBox="0 0 20 56"><path d="M18 2L2 28l16 26" fill="none" stroke="#fff" stroke-width="1.5"/></svg>
<svg class="hero-arrow abs" style="left:1124px" viewBox="0 0 20 56"><path d="M2 2l16 26L2 54" fill="none" stroke="#fff" stroke-width="1.5"/></svg>
<svg class="hero-wave abs" viewBox="0 0 1200 230" preserveAspectRatio="none">
  <path d="M0 230V150C200 50 450 75 700 70 900 66 1050 40 1200 20V230z" fill="#9bcb3c"/>
  <path d="M0 230V200C180 80 420 82 700 78 900 75 1060 52 1200 30V230z" fill="#3377b5"/>
  <path d="M0 230V214C190 92 430 88 700 84 900 81 1060 62 1200 42V230z" fill="#fff"/>
</svg>

<h2 class="section-title abs" style="top:811px">WELCOME TO SUNSET HARBOR LIVING</h2>
<div class="title-accent abs" style="top:855px" role="img" aria-label="Blue brush ornament"></div>
<p class="welcome-text abs">Sed ut perspiciatis unde omnis iste natus error sit voluptatem accusantium doloremque laudantium, totam rem aperiam, eaque ipsa quae ab illo inventore veritatis et quasi architecto beatae vitae dicta sunt explicabo. Nemo enim ipsam voluptatem quia voluptas sit aspernatur aut odit aut fugit, sed quia consequuntur magni dolores eos qui ratione voluptatem sequi nesciunt</p>

<div class="feature abs" style="left:98px">
  <div class="feature-icon"><svg width="28" height="28" viewBox="0 0 28 28"><circle cx="14" cy="14" r="12" fill="#9bcb3c"/><path d="M8 9c3 0 4 2 6 2s1 4-2 4-2 4-5 3M17 17c2-1 4 0 5 2" fill="none" stroke="#fff" stroke-width="1.6"/></svg></div>
  <div><h3>Insurance &amp; Health care</h3><p>Accusantium doloremque aperiam, eaque ipsa quae ab illo inventore...</p></div>
</div>
<div class="feature abs" style="left:444px">
  <div class="feature-icon"><svg width="20" height="28" viewBox="0 0 20 28"><path d="M10 1C5 1 1 5 1 10c0 7 9 17 9 17s9-10 9-17c0-5-4-9-9-9z" fill="#9bcb3c"/><circle cx="10" cy="10" r="3.5" fill="#fff"/></svg></div>
  <div><h3>Mediacl Tourism</h3><p>Accusantium doloremque aperiam, eaque ipsa quae ab illo inventore...</p></div>
</div>
<div class="feature abs" style="left:796px">
  <div class="feature-icon"><svg width="30" height="26" viewBox="0 0 30 26"><circle cx="15" cy="7" r="5" fill="#9bcb3c"/><circle cx="6" cy="10" r="3.5" fill="#9bcb3c"/><circle cx="24" cy="10" r="3.5" fill="#9bcb3c"/><path d="M7 25c0-7 4-11 8-11s8 4 8 11zM0 23c0-5 2-8 6-8 1 0 2 1 2 1-2 2-3 5-3 7zM30 23c0-5-2-8-6-8-1 0-2 1-2 1 2 2 3 5 3 7z" fill="#9bcb3c"/></svg></div>
  <div><h3>Cost of Living</h3><p>Accusantium doloremque aperiam, eaque ipsa quae ab illo inventore...</p></div>
</div>

<section class="destinations abs">
  <h2 class="section-title abs" style="top:47px">TRAVEL DESTINATIONS</h2>
  <div class="title-accent light abs" style="top:91px" role="img" aria-label="White brush ornament"></div>
</section>
<article class="card abs" style="left:99px">
  <div class="card-photo" role="img" aria-label="Photo of an elephant ride near temple ruins in Thailand" style="background:linear-gradient(#4aa3e0 0%,#9fd2f0 45%,#4f9a2e 60%,#3f7d25 100%)"></div>
  <h3>THAILAND</h3><p>Selum quidolorem eumuo volup tased<br>nulla parenim admin...</p><span class="btn-more">View More Info!</span>
</article>
<article class="card abs" style="left:357px">
  <div class="card-photo" role="img" aria-label="Photo of a city skyline at dusk in Malaysia" style="background:linear-gradient(#5a6fb5 0%,#c77a7a 45%,#3a5b45 75%,#2d4a2e 100%)"></div>
  <h3>MALAYSIA</h3><p>Selum quidolorem eumuo volup tased<br>nulla parenim admin...</p><span class="btn-more">View More Info!</span>
</article>
<article class="card abs" style="left:613px">
  <div class="card-photo" role="img" aria-label="Photo of a lakeside temple in Indonesia with mountains" style="background:linear-gradient(#8fb3d1 0%,#6f8c8f 45%,#3d4a44 65%,#8fa9b8 100%)"></div>
  <h3>INDONESIA</h3><p>Selum quidolorem eumuo volup tased<br>nulla parenim admin...</p><span class="btn-more">View More Info!</span>
</article>
<article class="card abs" style="left:870px">
  <div class="card-photo" role="img" aria-label="Photo of a tropical beach with palm trees and a hammock in the Philippines" style="background:linear-gradient(#2f7fd0 0%,#8cc8ee 40%,#5bb8c8 60%,#e8dcb8 100%)"></div>
  <h3>PHILIPPINES</h3><p>Selum quidolorem eumuo volup tased<br>nulla parenim admin...</p><span class="btn-more">View More Info!</span>
</article>

<svg class="newsletter-band abs" viewBox="0 0 1200 280" preserveAspectRatio="none">
  <path d="M0 0C150 70 350 100 600 95 850 90 1050 70 1200 95V280H0z" fill="#9bcb3c"/>
  <path d="M0 0C150 70 350 100 600 95 850 90 1050 70 1200 95" fill="none" stroke="#3377b5" stroke-width="4"/>
</svg>

<h2 class="section-title abs" style="top:1705px">WEEKLY BLOGS &amp; ARTICLES</h2>
<div class="title-accent abs" style="top:1749px" role="img" aria-label="Blue brush ornament"></div>

<article class="post abs" style="left:99px">
  <div class="post-photo" role="img" aria-label="Photo of a happy retired couple outdoors" style="background:linear-gradient(120deg,#8aa3b8,#c9a98a 55%,#6a7c8c)"></div>
  <div><h4>ACCUSANTIUM DOLOREMQUE REM APERIAM</h4><div class="post-date">Posted on 24 March 2016</div><p class="post-text">Sed ut perspiciatis unde omnis iste natus error sit voluptatem accusantium doloremque laudantium, totam rem aperiam, eaque ipsa quae</p><div class="post-meta"><span class="stars">★★★★<span style="color:#999">★</span></span><span>👍 12 Reviews</span></div></div>
</article>
<article class="post abs" style="left:629px">
  <div class="post-photo" role="img" aria-label="Photo of a retired couple in front of an ornate temple" style="background:linear-gradient(120deg,#6fa8dc,#d6a553 55%,#9b6a3a)"></div>
  <div><h4>ACCUSANTIUM DOLOREMQUE REM APERIAM</h4><div class="post-date">Posted on 24 March 2016</div><p class="post-text">Sed ut perspiciatis unde omnis iste natus error sit voluptatem accusantium doloremque laudantium, totam rem aperiam, eaque ipsa quae</p><div class="post-meta"><span class="stars">★★★★<span style="color:#999">★</span></span><span>👍 12 Reviews</span></div></div>
</article>

<svg class="abs" style="left:98px;top:2108px" width="56" height="48" viewBox="0 0 56 48"><path d="M4 14L44 2l8 30-40 12z" fill="#fff"/><path d="M4 14l26 14 22-24" fill="none" stroke="#9bcb3c" stroke-width="2"/></svg>
<div class="news-label abs"><span>NEWSLETTER</span><strong>SUBSCRIPTION</strong></div>
<div class="field abs" style="left:371px">Your Name*</div>
<div class="field abs" style="left:673px">Your E-mail*</div>
<div class="btn-signup abs">SIGN UP</div>

<footer class="site-footer abs">
  <div class="socials"><span></span><span></span><span></span><span></span><span></span></div>
  <div class="footer-links">Home &nbsp;|&nbsp; Visa Property &nbsp;|&nbsp; Financials &nbsp;|&nbsp; Travel &nbsp;|&nbsp; Insurance &amp; Healthcare &nbsp;|&nbsp; Medical Tourism &nbsp;|&nbsp; Cost of Living<br>Weekly Blogs and Articles &nbsp;|&nbsp; Sunset Harbor Living Story &nbsp;|&nbsp; Contact Us</div>
  <div class="copyright">Copyrights©Sunset Harbor Living 2016 | Allrights Resserved.</div>
</footer>

</body>
</html>
```